Brightwell Aero Services Logo

I need a website and logo for the parent company Brightwell Aero Services, which encompasses general aviation aircraft repair, small aircrat rental and flight school. The company is based in Ashcombe Ridge, Kestrel at the Tolleson county airport. A saying that can be incorporated somehere could be, "Quality flying is safe flying", "Safety in mind is no accident" ,. I need a website and logo.

The company started as a repair shop performing repairs and inspections on Harlan, Vantor, Delkin and Ralstead general aviation aircraft, all models of single engine piston, multi engine piston, and single engine turboprop with an emphasis on Harlan Solvane and AeroTurn turbo prop aircraft. We have se=ince entered the aircraft rental and flight instruction market using the Delkin 240 ang Harlan Ranger aircraft.

Number of Pages; I don't know. Maybe 5 ? A home page for Brightwell Aero Services, page for maintenance and repairs and a couple for the rental and school. The maintenance shop is busy, always has been. I need to get the rental and school advertised and busy.

I have a logo for the maintenance shop shirts, not for the school. I do not have the file. I paid a business locally to do that and print on the shirts. They have the file.

Target Market(s)

In our flight school rental fleet department, we are looking for persons wishing to obtain their private pilot license and continuing on into their commercial and instrument ratings. In the aircraft maintenance department, we are looking for new customers who want a better and more quality relationship with their aircraft maintenance provider who will give more detail and quality in the repairs with an emphasis on safety and fewer problems between scheduled maintenance cycles on their aircraft. Brightwell's owner, Dale Hutchins, has been performing aircraft maintenance in the Atlanta area for 27 years. He has built a steady customer base through those years.

```html
<!DOCTYPE html>
<html lang="en">
<head>
<meta charset="utf-8">
<title>Brightwell Aero Services</title>
<link rel="stylesheet" href="https://fonts.googleapis.com/css2?family=Abel&family=Mulish:wght@400;600&display=swap">
<style>
:root{
  --teal:#2291b5;
  --navy:#163d6e;
  --ink:#333;
  --muted:#555;
  --panel:#f0f0f0;
  --line-blue:#cfe3ea;
  --white:#fff;
}
*{box-sizing:border-box;margin:0;padding:0}
html,body{width:1200px;height:4335px;overflow:hidden;background:#fff}
body{font-family:'Mulish',sans-serif;color:var(--ink)}
.page{position:relative;width:1200px;height:4335px;overflow:hidden}
.abs{position:absolute}
.heading{font-family:'Abel',sans-serif;color:var(--navy);font-weight:400}
.rule{position:absolute;height:3px;width:48px;background:var(--teal)}
.btn{position:absolute;background:var(--teal);color:#fff;font-family:'Abel',sans-serif;font-size:13px;display:flex;align-items:center;justify-content:center;letter-spacing:.3px;gap:6px}
.copy{font-size:12.5px;line-height:23px;color:var(--muted)}
.copy p+p{margin-top:6px}
.photo{position:absolute}

/* header */
.brand{position:absolute;display:flex;align-items:center;gap:10px}
.brand-dot{width:22px;height:22px;border-radius:50%;background:var(--navy)}
.brand-name{font-family:'Abel',sans-serif;font-size:22px;color:var(--navy);line-height:1}
.nav{position:absolute;top:32px;left:503px;display:flex;gap:28px;font-family:'Abel',sans-serif;font-size:12.5px;color:#222}
.nav .active{color:var(--teal)}

/* hero */
.hero-card{position:absolute;left:0;top:163px;width:569px;height:406px;background:#fff}
.hero-l1{left:161px;top:228px;font-size:52px;color:#222;font-family:'Abel',sans-serif}
.hero-l2{left:157px;top:288px;font-size:84px;color:#222;font-family:'Abel',sans-serif;line-height:1}
.hero-l3{left:162px;top:392px;font-size:31px;color:#222;font-family:'Abel',sans-serif}

/* services */
.section-title{position:absolute;left:0;width:1200px;text-align:center;font-size:33px}
.card-title{position:absolute;font-family:'Abel',sans-serif;font-size:17px;color:#222}
.plus{position:absolute;width:20px;height:20px}

/* reviews */
.review{position:absolute;top:2075px;width:425px;height:200px;background:#fff;text-align:center}
.review .name{position:absolute;top:58px;width:100%;font-family:'Abel',sans-serif;font-size:17px;color:var(--teal)}
.review .copy{position:absolute;top:92px;left:20px;right:20px;font-size:12.5px;line-height:23px}
.review .bar{position:absolute;left:16px;right:16px;bottom:-7px;height:8px;background:var(--line-blue)}
.avatar{position:absolute;width:88px;height:88px;border-radius:50%;border:3px solid var(--teal);background:linear-gradient(#c9c9c9,#8c8c8c)}
.arrow{position:absolute;width:40px;height:40px;border-radius:50%;background:#fff;display:flex;align-items:center;justify-content:center}

/* rental list */
.checks{list-style:none;font-size:12.5px;color:var(--muted)}
.checks li{height:27px;display:flex;align-items:center;gap:7px}

/* footer */
.footer{position:absolute;left:0;top:3923px;width:1200px;height:412px;background:linear-gradient(180deg,#1f4674 0%,#173a63 60%,#143257 100%)}
.footer-brand{position:absolute;left:0;width:1200px;top:88px;display:flex;justify-content:center;align-items:center;gap:12px}
.footer-brand .brand-name{color:#fff;font-size:30px}
.footer-brand .brand-dot{background:#fff;width:28px;height:28px}
.footer-nav{position:absolute;top:180px;left:0;width:1200px;display:flex;justify-content:center;gap:28px;font-family:'Abel',sans-serif;font-size:12px;color:#fff}
.contact{position:absolute;top:268px;display:flex;gap:18px;align-items:center;color:#fff;font-size:12.5px;line-height:19px}
.contact .ico{width:36px;height:36px;background:var(--teal);display:flex;align-items:center;justify-content:center}
.contact b{font-weight:600}
.copyright{position:absolute;left:163px;top:370px;font-size:12px;color:#dde6ef}
.social{position:absolute;top:372px;width:14px;height:14px;border-radius:50%;background:#fff}
</style>
</head>
<body>
<div class="page">

  <header>
    <div class="brand" style="left:161px;top:28px">
      <span class="brand-dot"></span>
      <span class="brand-name">Brightwell Aero Services</span>
    </div>
    <nav class="nav">
      <span class="active">HOME</span>
      <span>MAINTENANCE &amp; REPAIRS</span>
      <span>AIRCRAFT RENTAL</span>
      <span>FLIGHT SCHOOL</span>
      <span>CONTACT US</span>
    </nav>
  </header>

  <section class="hero">
    <div class="photo" role="img" aria-label="Hangar interior with a white twin-engine aircraft under maintenance" style="left:496px;top:79px;width:704px;height:574px;background:linear-gradient(160deg,#7a736a 0%,#5d5852 35%,#b9b6b1 65%,#8a7f70 100%)"></div>
    <div class="hero-card"></div>
    <div class="abs hero-l1">Quality Flying is</div>
    <div class="abs hero-l2">Safe Flying</div>
    <div class="abs hero-l3">Safety In Mind is No Accident</div>
    <div class="btn" style="left:161px;top:451px;width:139px;height:44px;font-size:14px">CONTACT US</div>
  </section>

  <section class="services">
    <h2 class="heading section-title" style="top:733px">OUR SERVICES</h2>
    <div class="rule" style="left:576px;top:787px"></div>

    <div class="abs" style="left:148px;top:836px;width:274px;height:319px;border:2px solid var(--teal)"></div>
    <div class="photo" role="img" aria-label="Instructor and student beside a propeller aircraft in a hangar" style="left:161px;top:823px;width:277px;height:232px;background:linear-gradient(150deg,#4b4a4a,#8b8682 55%,#d8d6d3)"></div>
    <div class="card-title" style="left:177px;top:1072px">Flight School</div>
    <div class="abs copy" style="left:177px;top:1096px;width:200px;font-size:12px;line-height:20px">Lorem ipsum dolor sit amet, consectetuer adipiscing.</div>
    <svg class="plus" style="left:381px;top:1111px" viewBox="0 0 20 20"><path d="M10 0v20M0 10h20" stroke="#333" stroke-width="2"/></svg>

    <div class="photo" role="img" aria-label="Small red and white aircraft parked on a runway" style="left:461px;top:823px;width:277px;height:232px;background:linear-gradient(180deg,#d7cdcf 0%,#cdc5c7 60%,#8d8a88 100%)"></div>
    <div class="card-title" style="left:461px;top:1072px">Small Aircraft Rental</div>
    <svg class="plus" style="left:719px;top:1111px" viewBox="0 0 20 20"><path d="M10 0v20M0 10h20" stroke="#333" stroke-width="2"/></svg>

    <div class="photo" role="img" aria-label="Several aircraft parked inside a repair hangar" style="left:762px;top:823px;width:277px;height:232px;background:linear-gradient(160deg,#6b6c64,#8f8d85 45%,#c8c5bf)"></div>
    <div class="card-title" style="left:762px;top:1072px">Aircraft Repair</div>
    <svg class="plus" style="left:1019px;top:1111px" viewBox="0 0 20 20"><path d="M10 0v20M0 10h20" stroke="#333" stroke-width="2"/></svg>

    <div class="btn" style="left:545px;top:1192px;width:108px;height:37px">CONTACT US</div>
  </section>

  <section class="about">
    <div class="abs" style="left:522px;top:1319px;width:678px;height:398px;background:var(--panel)"></div>
    <div class="abs" style="left:241px;top:1377px;width:104px;height:12px;background:var(--navy)"></div>
    <div class="abs" style="left:72px;top:1463px;width:122px;height:2px;background:var(--teal)"></div>
    <div class="photo" role="img" aria-label="White single-engine aircraft taxiing with trees behind" style="left:161px;top:1389px;width:426px;height:363px;background:linear-gradient(180deg,#2f4a2a 0%,#4f6a3e 45%,#9aa08f 72%,#6b6d5e 100%)"></div>
    <h2 class="heading abs" style="left:626px;top:1376px;font-size:32px;line-height:34px">About<br>Brightwell Aero Services</h2>
    <div class="rule" style="left:626px;top:1460px"></div>
    <div class="abs copy" style="left:626px;top:1481px;width:410px">
      <p>Lorem ipsum dolor sit amet, consectetur adipiscing elit, sed do eiusmod tempor incididunt ut labore et dolore magna aliqua. Ut enim ad minim veniam quis nostrud.</p>
      <p>Quis autem vel eum iure reprehenderit qui in ea voluptate velit esse quam nihil molestiae consequatur...</p>
    </div>
    <div class="btn" style="left:626px;top:1619px;width:98px;height:37px">READ MORE</div>
  </section>

  <section class="reviews">
    <div class="abs" style="left:0;top:1846px;width:1200px;height:527px;background:var(--panel)"></div>
    <h2 class="heading section-title" style="top:1936px">CUSTOMER REVIEWS</h2>
    <div class="rule" style="left:576px;top:1991px"></div>

    <div class="review" style="left:161px">
      <div class="name">Tobin Marsh</div>
      <div class="copy">Lorem ipsum dolor sit amet, consectetur adipiscing elit, sed do eiusmod tempor incididunt ut labore et dolore magna aliqua. Ut enim ad minim veniam Nemo enim ipsam voluptatem quia voluptas sit aspernatur...</div>
      <div class="bar"></div>
    </div>
    <div class="avatar" role="img" aria-label="Portrait of customer Tobin Marsh" style="left:329px;top:2029px"></div>

    <div class="review" style="left:614px">
      <div class="name">Lena Farrow</div>
      <div class="copy">Lorem ipsum dolor sit amet, consectetur adipiscing elit, sed do eiusmod tempor incididunt ut labore et dolore magna aliqua. Ut enim ad minim veniam Nemo enim ipsam voluptatem quia voluptas sit aspernatur...</div>
      <div class="bar"></div>
    </div>
    <div class="avatar" role="img" aria-label="Portrait of customer Lena Farrow" style="left:782px;top:2029px"></div>

    <div class="arrow" style="left:81px;top:2158px"><svg width="12" height="12" viewBox="0 0 12 12"><path d="M8 1L3 6l5 5" fill="none" stroke="#222" stroke-width="2"/></svg></div>
    <div class="arrow" style="left:1079px;top:2155px"><svg width="12" height="12" viewBox="0 0 12 12"><path d="M4 1l5 5-5 5" fill="none" stroke="#2291b5" stroke-width="2"/></svg></div>
  </section>

  <section class="schools">
    <div class="abs" style="left:522px;top:2462px;width:678px;height:396px;background:var(--panel)"></div>
    <div class="abs" style="left:241px;top:2516px;width:104px;height:12px;background:var(--navy)"></div>
    <div class="abs" style="left:72px;top:2605px;width:122px;height:2px;background:var(--teal)"></div>
    <div class="photo" role="img" aria-label="Pilot in the cockpit of a white and blue high-wing light aircraft" style="left:161px;top:2531px;width:426px;height:364px;background:linear-gradient(160deg,#e6e8ea 0%,#b9bfc6 40%,#6f7d6a 75%,#4d6140 100%)"></div>
    <h2 class="heading abs" style="left:626px;top:2516px;font-size:32px">OUR FLIGHT SCHOOLS</h2>
    <div class="rule" style="left:626px;top:2568px"></div>
    <div class="abs copy" style="left:626px;top:2589px;width:420px">
      <p>Lorem ipsum dolor sit amet, consectetur adipiscing elit Nunc vulputate eleifend mi, sit amet semper urna acsan at.</p>
      <p style="margin-top:10px">Lorem ipsum dolor sit amet, consectetuer adipiscing elit, sed diam nonummy nibh euismod tincidunt ut laoreet dor magna aliquam erat volutpat. Ut wisi enim ad minim ve quis nostrud exerci tation ullamcorper quis nostrud suscipit...</p>
    </div>
    <div class="btn" style="left:626px;top:2765px;width:99px;height:36px">READ MORE</div>
  </section>

  <section class="rental">
    <div class="photo" role="img" aria-label="High-wing rental aircraft parked on a grass airfield under a blue sky" style="left:0;top:2987px;width:1200px;height:608px;background:linear-gradient(180deg,#7ea7d6 0%,#a9c6e6 52%,#b9c9c2 60%,#5a8a3a 66%,#4a7f2e 100%)"></div>
    <div class="abs" style="left:161px;top:3078px;width:495px;height:426px;background:var(--panel)"></div>
    <h2 class="heading abs" style="left:219px;top:3129px;font-size:32px">OUR FLIGHT RENTAL</h2>
    <div class="rule" style="left:219px;top:3182px"></div>
    <div class="abs copy" style="left:219px;top:3204px;width:400px">Lorem ipsum dolor sit amet, consectetur adipiscing elit Nunc vulputate eleifend mi, sit amet semper urna acsan at.</div>
    <ul class="checks abs" style="left:219px;top:3259px">
      <li><svg width="12" height="12" viewBox="0 0 12 12"><rect x="0.5" y="0.5" width="11" height="11" fill="none" stroke="#2291b5"/><path d="M2.5 6l2.5 2.5 5-6" fill="none" stroke="#2291b5" stroke-width="1.6"/></svg>Lorem ipsum dolor sit amet consectetur adipiscing.</li>
      <li><svg width="12" height="12" viewBox="0 0 12 12"><rect x="0.5" y="0.5" width="11" height="11" fill="none" stroke="#2291b5"/><path d="M2.5 6l2.5 2.5 5-6" fill="none" stroke="#2291b5" stroke-width="1.6"/></svg>Ut enim ad minim veniam quis nostrud semper.</li>
      <li><svg width="12" height="12" viewBox="0 0 12 12"><rect x="0.5" y="0.5" width="11" height="11" fill="none" stroke="#2291b5"/><path d="M2.5 6l2.5 2.5 5-6" fill="none" stroke="#2291b5" stroke-width="1.6"/></svg>laboris nisi ut aliquip ex ea commodo consequat.</li>
      <li><svg width="12" height="12" viewBox="0 0 12 12"><rect x="0.5" y="0.5" width="11" height="11" fill="none" stroke="#2291b5"/><path d="M2.5 6l2.5 2.5 5-6" fill="none" stroke="#2291b5" stroke-width="1.6"/></svg>Duis aute irure dolor in reprehenderit involuptate.</li>
      <li><svg width="12" height="12" viewBox="0 0 12 12"><rect x="0.5" y="0.5" width="11" height="11" fill="none" stroke="#2291b5"/><path d="M2.5 6l2.5 2.5 5-6" fill="none" stroke="#2291b5" stroke-width="1.6"/></svg>Nostrum exercitationem ullam corporis.</li>
    </ul>
    <div class="btn" style="left:219px;top:3411px;width:116px;height:34px">
      <svg width="11" height="11" viewBox="0 0 11 11"><rect x="0.5" y="1.5" width="10" height="9" fill="none" stroke="#fff"/><path d="M0.5 4h10M3 0v3M8 0v3" stroke="#fff"/></svg>BOOK NOW</div>
  </section>

  <section class="cta">
    <h2 class="heading abs" style="left:0;width:1200px;text-align:center;top:3676px;font-size:33px">Lorem Ipsum Dolor Sit Amet Conse Ctetur</h2>
    <p class="abs" style="left:0;width:1200px;text-align:center;top:3727px;font-size:15.5px;line-height:29px;color:var(--muted)">At vero eos et accusamus et iusto odio dignissimos ducimus qui blanditiis praesentium voluptatum<br>deleniti atque corrupti quos dolores et quas molestias excepturi sint.</p>
    <div class="btn" style="left:547px;top:3797px;width:108px;height:34px">CONTACT US</div>
  </section>

  <footer class="footer">
    <div class="footer-brand">
      <span class="brand-dot"></span>
      <span class="brand-name">Brightwell Aero Services</span>
    </div>
    <nav class="footer-nav">
      <span>HOME</span><span>MAINTENANCE &amp; REPAIRS</span><span>AIRCRAFT RENTAL</span><span>FLIGHT SCHOOL</span><span>CONTACT US</span>
    </nav>

    <div class="contact" style="left:244px">
      <span class="ico"><svg width="16" height="18" viewBox="0 0 16 18"><path d="M8 1a6 6 0 0 0-6 6c0 4.5 6 10 6 10s6-5.5 6-10a6 6 0 0 0-6-6z" fill="#fff"/><circle cx="8" cy="7" r="2.2" fill="#2291b5"/></svg></span>
      <span>Lorem Ipsum Dolor Sit<br>Ashcombe Ridge, Kestrel</span>
    </div>
    <div class="contact" style="left:540px">
      <span class="ico"><svg width="16" height="16" viewBox="0 0 16 16"><path d="M4 1l3 3-1.6 2a9 9 0 0 0 4.6 4.6L12 9l3 3-2 3C7 15 1 9 1 3z" fill="#fff"/></svg></span>
      <span><b>PHONE</b><br>123 456 7890</span>
    </div>
    <div class="contact" style="left:779px">
      <span class="ico"><svg width="16" height="16" viewBox="0 0 16 16"><path d="M15 1L1 7l5 2 1 5 2.5-3.5L13 13z" fill="#fff"/></svg></span>
      <span><b>EMAIL</b><br>info@brightwellaero.com</span>
    </div>

    <div class="copyright">© 2022 Brightwell Aero Services. All Rights Reserved.</div>
    <span class="social" style="left:914px"></span>
    <span class="social" style="left:947px"></span>
    <span class="social" style="left:983px"></span>
    <span class="social" style="left:1021px"></span>
  </footer>

</div>
</body>
</html>
```